Lurro - coded wordpress homepage needed for modern real estate business

I need a one page website created for Lurro a cutting edge real estate agency. Please read the must haves for more information on the design. The website must be created into a wordpress theme and the winning designer must install wordpress and the site into my hosting included as part of this project. The site must also be secure and perform well with optimised images etc.

Ongoing work is available for the right person. More instructions include the website sections/content can be found here https://sheets.pelvano.net/page/d/7TrKbWnzQe_c48HsJfLoPiaZt-R2mYdBxVgN-oEkWjPX/view?mode=shared

Coding

Coded - Design and coding required

Colors

Designer to choose colors to be used in the design.

Requirements
Must have
• The project must be a modern, cutting edge website created in a similar style to leading modern brands. It must have flat graphics and look very good. Most real estate websites are not very good and I want this website to be the best in the industry.
• It must also be responsive and look good on mobile as well as desktop. Please make desktop versions first and if you are likely to be the designer I choose then I will get you to make up a mobile mock up once the website is almost done. Please design the site however you feel best and I will provide feedback from there. I am getting the logo created at the moment in another design competition so please use a mock logo for now and when the logo is finalised I will upload it in this brief. The logo will be white/red and the colour palette of the website needs to be dark. The red colour used must be #e60611 or CMYK C - 3% M - 100% Y - 100% K - 1% or RGB R - 230 G - 6 B - 17.
• Any questions just ask me, look forward to seeing your designs

```html
<!DOCTYPE html>
<html lang="en">
<head>
<meta charset="utf-8">
<title>Lurro – Homepage Concepts</title>
<link href="https://fonts.googleapis.com/css2?family=Poppins:ital,wght@0,400;0,500;0,600;0,700;1,400&display=swap" rel="stylesheet">
<style>
:root{
  --red:#e60611;
  --stage:#8c8c8c;
  --black:#000;
  --charcoal:#2b2b2b;
  --footer:#111;
  --white:#fff;
  --panel:#efefef;
  --muted:#777;
}
*{box-sizing:border-box;margin:0;padding:0}
html,body{width:1200px;height:2548px;overflow:hidden}
body{background:var(--stage);font-family:'Poppins',sans-serif;position:relative;color:var(--white)}
.page{position:absolute;top:31px;width:538px;overflow:hidden}
.page--dark{left:35px;--alt-bg:var(--black);--alt-ink:var(--white)}
.page--light{left:611px;--alt-bg:var(--white);--alt-ink:#111}
.sec{position:relative;overflow:hidden}
h2{font-weight:700;font-size:14.5px;line-height:1.05;letter-spacing:-.2px;text-transform:uppercase}
.small{font-size:5.3px;line-height:2.3}
.btn{display:inline-block;background:var(--red);color:#fff;font-weight:700;font-size:6.5px;padding:5px 7px;text-transform:uppercase;border:1px solid #fff}
.btn--plain{border-color:var(--red)}
.ticks{list-style:none}
.ticks li{position:relative;padding-left:10px}
.ticks li::before{content:"";position:absolute;left:0;top:4px;width:5px;height:5px;border-radius:50%;background:var(--red);box-shadow:inset 0 0 0 1.3px currentColor}
.ticks--light li::before{background:transparent;border:1px solid #fff}
.photo{position:absolute}
/* top bar */
.topbar{height:19px;background:var(--red);display:flex;justify-content:flex-end;align-items:center;gap:10px;padding-right:28px;font-size:7.2px;font-weight:600}
/* hero */
.hero{height:270px}
.hero .photo{inset:0;background:linear-gradient(180deg,#8ea3b4 0%,#6d7f6c 18%,#3f5236 45%,#33452c 75%,#4b5a40 100%)}
.hero .photo::after{content:"";position:absolute;inset:0;background:rgba(0,0,0,.25)}
.nav{position:absolute;top:0;left:50px;right:40px;height:45px;display:flex;align-items:center;z-index:2}
.logo{display:flex;align-items:center;gap:5px;font-weight:700;font-size:12px;letter-spacing:.5px}
.logo i{width:8px;height:8px;background:var(--red)}
.nav ul{list-style:none;display:flex;gap:22px;margin-left:56px;font-size:6.2px;font-weight:500}
.nav li:first-child{border-bottom:1px solid #fff}
.hero-copy{position:absolute;top:100px;width:100%;text-align:center;z-index:2}
.hero-copy h1{font-size:14.5px;font-weight:700}
.hero-copy p{font-size:9px;font-weight:500;line-height:1.3;width:340px;margin:4px auto 7px}
.dots{position:absolute;bottom:20px;width:100%;display:flex;justify-content:center;gap:6px;z-index:2}
.dots span{width:6px;height:6px;border-radius:50%;border:1px solid #fff}
.dots span:nth-child(2){background:#fff}
/* appraisal */
.appraisal{height:195px;background:var(--alt-bg);color:var(--alt-ink);display:flex;padding:40px 50px 0}
.appraisal .left{width:222px}
.appraisal .left h2{margin-bottom:7px}
.appraisal .left li{font-size:6px;font-weight:500;line-height:2.15}
.form-panel{width:220px;height:122px;background:var(--panel);border:1px solid #ddd;color:#111;text-align:center;padding:10px 10px 0}
.form-panel h3{font-size:9.5px;font-weight:500;margin-bottom:6px}
.fields{display:grid;grid-template-columns:1fr 1fr;gap:7px 8px;margin-bottom:8px}
.field{height:19px;background:#fff;border:1px solid #ddd;font-size:5.5px;color:#777;text-align:left;padding:5px}
/* split */
.split{display:flex}
.split > div{width:50%;position:relative}
.different{height:254px}
.different .photo{inset:0;background:linear-gradient(170deg,#93a6b6 0%,#5e7158 12%,#2f4327 50%,#3d4f33 100%)}
.red{background:var(--red)}
.different .copy{padding:26px 12px 0 10px}
.different h2{margin-bottom:8px}
.different li{font-size:5.4px;line-height:2.35}
/* testimonials */
.testi{height:189px;background:var(--charcoal);text-align:center;padding-top:34px}
.testi .sub{font-size:6.2px;font-weight:500;margin:3px 0 5px}
.avatar{width:38px;height:38px;border-radius:50%;margin:0 auto 8px;background:linear-gradient(#cfd5da,#9aa3aa);border:2px solid #fff}
.testi p{font-size:5.6px;line-height:2.25;width:300px;margin:0 auto}
.arrow{position:absolute;width:18px;height:18px;border-radius:50%;border:1px solid currentColor;display:flex;align-items:center;justify-content:center}
.arrow svg{width:6px;height:6px}
/* listings */
.market{height:285px;background:var(--alt-bg);color:var(--alt-ink);text-align:center;padding-top:34px}
.market h2,.sold h2{margin-bottom:10px}
.cards{display:flex;gap:17px;justify-content:center;color:#111;text-align:left}
.card{width:136px;background:#fff;border:1px solid #ccc}
.card .img{height:75px;position:relative;background:linear-gradient(175deg,#a7b7c4 0%,#5c6f57 25%,#3a4e33 100%)}
.tag{position:absolute;top:7px;right:6px;background:var(--red);color:#fff;font-size:6px;font-weight:700;padding:1px 5px;border:1px solid #fff}
.price{position:absolute;bottom:6px;left:7px;right:6px;display:flex;justify-content:space-between;align-items:baseline;color:#fff}
.price b{font-size:9px}
.price span{font-size:5px}
.card .body{padding:6px 7px 4px}
.card h4{font-size:6.5px;font-weight:600;margin-bottom:2px}
.card p{font-size:5.4px;line-height:2.2;color:#555}
.meta{display:flex;gap:10px;font-size:5.3px;color:#444;margin-top:2px;padding-bottom:2px}
.meta i{display:inline-block;width:5px;height:4px;background:var(--red);margin-right:2px}
.spec-title{margin-top:30px}
/* marketing band */
.marketing{height:213px}
.marketing .red{background:linear-gradient(160deg,#e60611,#c8040f)}
.marketing .dark{background:linear-gradient(160deg,#262626,#121212)}
.marketing .copy{padding:36px 20px 0 50px}
.marketing .dark .copy{padding:36px 50px 0 20px}
.marketing h3{font-size:9.4px;font-weight:600;line-height:1.3;margin-bottom:6px}
.marketing li{font-size:5.3px;line-height:2.35}
.marketing .btn{margin-top:9px}
/* team */
.team{height:226px;background:var(--alt-bg);color:var(--alt-ink);display:flex;padding:38px 50px 0}
.team .intro{width:180px;padding-top:14px}
.team .intro p{font-size:5.4px;line-height:2.3;margin:6px 0 12px}
.member{width:118px;height:150px;background:#fff;border:1px solid #ccc;margin-left:15px;color:#111;text-align:center}
.member .img{height:96px;background:linear-gradient(180deg,#5f6b77,#3b4550);position:relative}
.member .img::after{content:"";position:absolute;top:8px;right:8px;width:10px;height:10px;border-radius:50%;background:#fff}
.member h4{font-size:9px;font-style:italic;font-weight:400;margin-top:4px}
.member .role{font-size:5.5px;color:var(--red)}
.socials{display:flex;justify-content:center;gap:5px;margin-top:4px}
.socials span{width:9px;height:9px;border-radius:50%;border:1px solid #999}
/* about */
.about{height:215px}
.about .photo{inset:0;background:linear-gradient(170deg,#7c8c78 0%,#556650 45%,#48573f 100%)}
.about .copy{padding:32px 14px 0 15px}
.about h2{margin-bottom:8px}
.about p{font-size:5.5px;line-height:2.3;text-align:justify;margin-bottom:12px}
/* sold */
.sold{height:245px;background:var(--alt-bg);color:var(--alt-ink);text-align:center;padding-top:34px}
.sold .card .img{height:86px}
/* touch */
.touch{height:229px}
.touch .copy{padding:20px 35px 0 50px}
.touch h2{margin-bottom:8px}
.input{height:19px;background:#fff;border:1px solid #ccc;color:#777;font-size:5.5px;padding:5px 9px;margin-bottom:8px}
.input--tall{height:43px}
.touch .photo{inset:0;background:linear-gradient(160deg,#e7d9c7 0%,#caa989 50%,#a77d57 100%)}
/* footer */
.footer{height:150px;background:var(--footer);padding:26px 50px 0;display:flex;gap:0;position:relative}
.footer h5{font-size:6px;font-weight:600;margin-bottom:6px}
.footer p{font-size:5.4px;line-height:2.4;color:#ddd}
.col1{width:150px}.col2{width:132px}.col3{width:160px}
.sub-row{display:flex;margin-top:6px}
.sub-row div{flex:1;height:16px;border:1px solid #aaa;font-size:5.3px;padding:4px 5px;color:#ddd}
.sub-row b{background:var(--red);font-size:6px;padding:4px 10px}
.f-icons{display:flex;gap:8px;margin-top:8px}
.f-icons span{width:8px;height:8px;border-radius:50%;background:#fff}
.copyright{position:absolute;bottom:6px;left:0;width:100%;text-align:center;font-size:5.5px;color:#ddd}
</style>
</head>
<body>

<!-- ============ DARK CONCEPT ============ -->
<main class="page page--dark">
  <div class="topbar"><span>✆ (321)-654-0987</span><span>✉ info@lurro.com</span></div>
  <section class="sec hero">
    <div class="photo" role="img" aria-label="Aerial photo of a river winding through a forested valley"></div>
    <nav class="nav"><div class="logo"><i></i>LURRO</div>
      <ul><li>HOME</li><li>ABOUT</li><li>MARKET</li><li>SEARCH LSTINGS</li><li>OUR LISTINGS</li><li>CONTACT US</li></ul></nav>
    <div class="hero-copy"><h1>REAL ESTATE DONE DIFFERENTLY</h1><p>We are exceptional in everything we do so you can have confidence depending on us</p><span class="btn">Get started</span></div>
    <div class="dots"><span></span><span></span><span></span></div>
  </section>
  <section class="sec appraisal">
    <div class="left"><h2>Organise a free market appraisal</h2>
      <ul class="ticks"><li>Get a current price indication and market update</li><li>Learn more on the process of selling your property with us</li><li>100% free with no hidden costs and absolutely no pressure or sales tactics</li><li>Meet with us face to face and ask us anything</li></ul></div>
    <div class="form-panel"><h3>LOREM IPSUM</h3><div class="fields"><div class="field">First Name</div><div class="field">Last Name</div><div class="field">Phone Number</div><div class="field">Email</div></div><span class="btn btn--plain">Submit</span></div>
  </section>
  <section class="sec split different">
    <div><div class="photo" role="img" aria-label="Aerial photo of a large home surrounded by bushland"></div></div>
    <div class="red copy"><h2>How we're different</h2>
      <ul class="ticks ticks--light"><li>Integrity - We are honest, reliable and trustworthy. We truly value all our clients and will go above and beyond.</li><li>Exclusive - We only take on a small number of listings every month to ensure we deliver a high standard of service to every single one of our clients.</li><li>Location - We ONLY sell properties in Ferndale, Oakbury and Stonecliff giving us an intimate knowledge of the market and area.</li><li>Technology - We utilise the latest technology in the real estate industry to enhance our capabilities and get the best possible results.</li><li>Local - We have been Hillmoor locals for over 25 years and are always only a phone call away or 5 minutes down the road if you would like to meet with us.</li></ul></div>
  </section>
  <section class="sec testi">
    <h2>Client testimonials</h2><div class="sub">Lorem ipsum dolor sit amet, consectetur adipiscing elit,</div>
    <div class="avatar" role="img" aria-label="Client portrait"></div>
    <p>Lorem ipsum dolor sit amet, consectetur adipiscing elit, sed do eiusmod tempor incididunt ut labore et dolore magna aliqua. Quis ipsum suspendisse ultrices gravida. Risus commodo viverra maecenas accumsan lacus vel facilisis.</p>
    <span class="arrow" style="left:52px;top:104px"><svg viewBox="0 0 6 6"><path d="M4 0L1 3l3 3" fill="none" stroke="#fff"/></svg></span>
    <span class="arrow" style="right:52px;top:104px"><svg viewBox="0 0 6 6"><path d="M2 0l3 3-3 3" fill="none" stroke="#fff"/></svg></span>
  </section>
  <section class="sec market">
    <h2>On the market</h2>
    <div class="cards">
      <div class="card"><div class="img" role="img" aria-label="Aerial view of river valley"><span class="tag">BUY</span><div class="price"><b>$45000</b><span>● Dummy Location</span></div></div><div class="body"><h4>Property Name Title</h4><p>Lorem ipsum dolor sit atur adipiscing elit, sed do eiusmod</p><div class="meta"><span><i></i>5 Beds</span><span><i></i>2 Baths</span><span><i></i>1500 ft2</span></div></div></div>
      <div class="card"><div class="img" role="img" aria-label="Aerial view of forested hills"><span class="tag">BUY</span><div class="price"><b>$45000</b><span>● Dummy Location</span></div></div><div class="body"><h4>Property Name Title</h4><p>Lorem ipsum dolor sit atur adipiscing elit, sed do eiusmod</p><div class="meta"><span><i></i>5 Beds</span><span><i></i>2 Baths</span><span><i></i>1500 ft2</span></div></div></div>
      <div class="card"><div class="img" role="img" aria-label="Aerial view of a suburb"><span class="tag">BUY</span><div class="price"><b>$45000</b><span>● Dummy Location</span></div></div><div class="body"><h4>Property Name Title</h4><p>Lorem ipsum dolor sit atur adipiscing elit, sed do eiusmod</p><div class="meta"><span><i></i>5 Beds</span><span><i></i>2 Baths</span><span><i></i>1500 ft2</span></div></div></div>
    </div>
    <span class="arrow" style="left:25px;top:135px"><svg viewBox="0 0 6 6"><path d="M4 0L1 3l3 3" fill="none" stroke="currentColor"/></svg></span>
    <span class="arrow" style="right:25px;top:135px"><svg viewBox="0 0 6 6"><path d="M2 0l3 3-3 3" fill="none" stroke="currentColor"/></svg></span>
    <h2 class="spec-title">Marketing is our specialty</h2>
  </section>
  <section class="sec split marketing">
    <div class="red"><div class="copy"><h3>Our marketing will supercharge the sale of your property by</h3><ul class="ticks ticks--light"><li>Creating more enquiries and therefore more prospective buyers</li><li>Putting you in a better negotiating position by having more prospective buyers</li><li>Giving you the best chance to maximise the sale price of your property</li></ul></div></div>
    <div class="dark"><div class="copy"><h3>This is achieved through our innovative marketing strategies including</h3><ul class="ticks ticks--light"><li>Use of the industry leading Customer Relationship Manager (CRM) Software as used by 40% of Australia's Top 100 Agents</li><li>Use of drones, professional videography and social media marketing</li><li>Top quality prospective buyer follow up and logging through utilising the capabilities of the CRM</li></ul><span class="btn">Read more ›</span></div></div>
  </section>
  <section class="sec team">
    <div class="intro"><h2>Meet the team</h2><p>Lorem ipsum dolor sit amet, consectetur adipiscing elit, sed do eiusmod tempor incididunt ut labore et dolore magna aliqua. Quis ipsum suspendisse ultrices gravida. Risus commodo viverra maecenas accumsan lacus vel facilisis.</p><span class="btn btn--plain">Meet the agent</span></div>
    <div class="member"><div class="img" role="img" aria-label="Agent portrait"></div><h4>Clara Benning</h4><div class="role">Licensee In Charge</div><div class="socials"><span></span><span></span><span></span></div></div>
    <div class="member"><div class="img" role="img" aria-label="Agent portrait"></div><h4>Dorian Hale</h4><div class="role">Sales Agent</div><div class="socials"><span></span><span></span><span></span></div></div>
  </section>
  <section class="sec split about">
    <div><div class="photo" role="img" aria-label="Aerial photo of a leafy suburban neighbourhood"></div></div>
    <div class="red copy"><h2>About Lurro</h2><p>Lorem ipsum dolor sit amet, consectetur adipiscing elit, sed do usmod tempor incididunt ut labore et dolore magna aliqua. Quis ipsum suspendisse ultrices gravida. Risus commodo viverra cenas accumsan lacus vel facilisis. Lorem ipsum dolor sit amet, tur iscing elit. Lorem ipsum dolor sit amet, consectetur adipiscing elit, sed do usmod tempor incididunt ut labore et dolore magna aliqua. Quis ipsum suspendisse ultrices gravida.</p><span class="btn">Read more ›</span></div>
  </section>
  <section class="sec sold">
    <h2>Recently sold</h2>
    <div class="cards">
      <div class="card"><div class="img" role="img" aria-label="Aerial view of a town"><span class="tag">SOLD</span></div><div class="body"><h4>Property Name Title</h4><p>$600/mo</p><div class="meta"><span><i></i>5 Beds</span><span><i></i>2 Baths</span><span><i></i>2019</span></div></div></div>
      <div class="card"><div class="img" role="img" aria-label="Aerial view of a town"><span class="tag">SOLD</span></div><div class="body"><h4>Property Name Title</h4><p>$600/mo</p><div class="meta"><span><i></i>5 Beds</span><span><i></i>2 Baths</span><span><i></i>2019</span></div></div></div>
      <div class="card"><div class="img" role="img" aria-label="Aerial view of a town"><span class="tag">SOLD</span></div><div class="body"><h4>Property Name Title</h4><p>$600/mo</p><div class="meta"><span><i></i>5 Beds</span><span><i></i>2 Baths</span><span><i></i>2019</span></div></div></div>
    </div>
    <span class="arrow" style="left:25px;top:135px"><svg viewBox="0 0 6 6"><path d="M4 0L1 3l3 3" fill="none" stroke="currentColor"/></svg></span>
    <span class="arrow" style="right:25px;top:135px"><svg viewBox="0 0 6 6"><path d="M2 0l3 3-3 3" fill="none" stroke="currentColor"/></svg></span>
  </section>
  <section class="sec split touch">
    <div class="red copy"><h2>Get in touch</h2><div class="input">Name</div><div class="input">Email</div><div class="input">Phone</div><div class="input input--tall">Message</div><span class="btn">Submit</span></div>
    <div><div class="photo" role="img" aria-label="Photo of a happy family unpacking moving boxes"></div></div>
  </section>
  <footer class="footer">
    <div class="col1"><h5>KEEP IN TOUCH</h5><p>● Main office<br>&nbsp;&nbsp;29th floor - Lorem Ipsum<br>&nbsp;&nbsp;street - London - UK<br>✆ Call us<br>&nbsp;&nbsp;(+01) 555.019.420<br>✉ Mail to<br>&nbsp;&nbsp;hello@lurro-mail.com</p></div>
    <div class="col2"><h5>INFORMATION</h5><p>About Us<br>Contact<br>Terms &amp; Conditions<br>Recent news<br>F.A.Qs</p></div>
    <div class="col3"><h5>NEWSLETTER</h5><p>Make sure that you're always the first who receive our latest news and promotion</p><div class="sub-row"><div>Your Email Address</div><b>SEND</b></div><div class="f-icons"><span></span><span></span><span></span><span></span><span></span></div></div>
    <div class="copyright">Copyright © 2019. All Rights Reserved | Privacy Policy | Terms of Use</div>
  </footer>
</main>

<!-- ============ LIGHT CONCEPT ============ -->
<main class="page page--light">
  <div class="topbar"><span>✆ (321)-654-0987</span><span>✉ info@lurro.com</span></div>
  <section class="sec hero">
    <div class="photo" role="img" aria-label="Aerial photo of a river winding through a forested valley"></div>
    <nav class="nav"><div class="logo"><i></i>LURRO</div>
      <ul><li>HOME</li><li>ABOUT</li><li>MARKET</li><li>SEARCH LSTINGS</li><li>OUR LISTINGS</li><li>CONTACT US</li></ul></nav>
    <div class="hero-copy"><h1>REAL ESTATE DONE DIFFERENTLY</h1><p>We are exceptional in everything we do so you can have confidence depending on us</p><span class="btn">Get started</span></div>
    <div class="dots"><span></span><span></span><span></span></div>
  </section>
  <section class="sec appraisal">
    <div class="left"><h2>Organise a free market appraisal</h2>
      <ul class="ticks"><li>Get a current price indication and market update</li><li>Learn more on the process of selling your property with us</li><li>100% free with no hidden costs and absolutely no pressure or sales tactics</li><li>Meet with us face to face and ask us anything</li></ul></div>
    <div class="form-panel"><h3>LOREM IPSUM</h3><div class="fields"><div class="field">First Name</div><div class="field">Last Name</div><div class="field">Phone Number</div><div class="field">Email</div></div><span class="btn btn--plain">Submit</span></div>
  </section>
  <section class="sec split different">
    <div><div class="photo" role="img" aria-label="Aerial photo of a large home surrounded by bushland"></div></div>
    <div class="red copy"><h2>How we're different</h2>
      <ul class="ticks ticks--light"><li>Integrity - We are honest, reliable and trustworthy. We truly value all our clients and will go above and beyond.</li><li>Exclusive - We only take on a small number of listings every month to ensure we deliver a high standard of service to every single one of our clients.</li><li>Location - We ONLY sell properties in Ferndale, Oakbury and Stonecliff giving us an intimate knowledge of the market and area.</li><li>Technology - We utilise the latest technology in the real estate industry to enhance our capabilities and get the best possible results.</li><li>Local - We have been Hillmoor locals for over 25 years and are always only a phone call away or 5 minutes down the road if you would like to meet with us.</li></ul></div>
  </section>
  <section class="sec testi">
    <h2>Client testimonials</h2><div class="sub">Lorem ipsum dolor sit amet, consectetur adipiscing elit,</div>
    <div class="avatar" role="img" aria-label="Client portrait"></div>
    <p>Lorem ipsum dolor sit amet, consectetur adipiscing elit, sed do eiusmod tempor incididunt ut labore et dolore magna aliqua. Quis ipsum suspendisse ultrices gravida. Risus commodo viverra maecenas accumsan lacus vel facilisis.</p>
    <span class="arrow" style="left:52px;top:104px"><svg viewBox="0 0 6 6"><path d="M4 0L1 3l3 3" fill="none" stroke="#fff"/></svg></span>
    <span class="arrow" style="right:52px;top:104px"><svg viewBox="0 0 6 6"><path d="M2 0l3 3-3 3" fill="none" stroke="#fff"/></svg></span>
  </section>
  <section class="sec market">
    <h2>On the market</h2>
    <div class="cards">
      <div class="card"><div class="img" role="img" aria-label="Aerial view of river valley"><span class="tag">BUY</span><div class="price"><b>$45000</b><span>● Dummy Location</span></div></div><div class="body"><h4>Property Name Title</h4><p>Lorem ipsum dolor sit atur adipiscing elit, sed do eiusmod</p><div class="meta"><span><i></i>5 Beds</span><span><i></i>2 Baths</span><span><i></i>1500 ft2</span></div></div></div>
      <div class="card"><div class="img" role="img" aria-label="Aerial view of forested hills"><span class="tag">BUY</span><div class="price"><b>$45000</b><span>● Dummy Location</span></div></div><div class="body"><h4>Property Name Title</h4><p>Lorem ipsum dolor sit atur adipiscing elit, sed do eiusmod</p><div class="meta"><span><i></i>5 Beds</span><span><i></i>2 Baths</span><span><i></i>1500 ft2</span></div></div></div>
      <div class="card"><div class="img" role="img" aria-label="Aerial view of a suburb"><span class="tag">BUY</span><div class="price"><b>$45000</b><span>● Dummy Location</span></div></div><div class="body"><h4>Property Name Title</h4><p>Lorem ipsum dolor sit atur adipiscing elit, sed do eiusmod</p><div class="meta"><span><i></i>5 Beds</span><span><i></i>2 Baths</span><span><i></i>1500 ft2</span></div></div></div>
    </div>
    <span class="arrow" style="left:25px;top:135px"><svg viewBox="0 0 6 6"><path d="M4 0L1 3l3 3" fill="none" stroke="currentColor"/></svg></span>
    <span class="arrow" style="right:25px;top:135px"><svg viewBox="0 0 6 6"><path d="M2 0l3 3-3 3" fill="none" stroke="currentColor"/></svg></span>
    <h2 class="spec-title">Marketing is our specialty</h2>
  </section>
  <section class="sec split marketing">
    <div class="red"><div class="copy"><h3>Our marketing will supercharge the sale of your property by</h3><ul class="ticks ticks--light"><li>Creating more enquiries and therefore more prospective buyers</li><li>Putting you in a better negotiating position by having more prospective buyers</li><li>Giving you the best chance to maximise the sale price of your property</li></ul></div></div>
    <div class="dark"><div class="copy"><h3>This is achieved through our innovative marketing strategies including</h3><ul class="ticks ticks--light"><li>Use of the industry leading Customer Relationship Manager (CRM) Software as used by 40% of Australia's Top 100 Agents</li><li>Use of drones, professional videography and social media marketing</li><li>Top quality prospective buyer follow up and logging through utilising the capabilities of the CRM</li></ul><span class="btn">Read more ›</span></div></div>
  </section>
  <section class="sec team">
    <div class="intro"><h2>Meet the team</h2><p>Lorem ipsum dolor sit amet, consectetur adipiscing elit, sed do eiusmod tempor incididunt ut labore et dolore magna aliqua. Quis ipsum suspendisse ultrices gravida. Risus commodo viverra maecenas accumsan lacus vel facilisis.</p><span class="btn btn--plain">Meet the agent</span></div>
    <div class="member"><div class="img" role="img" aria-label="Agent portrait"></div><h4>Clara Benning</h4><div class="role">Licensee In Charge</div><div class="socials"><span></span><span></span><span></span></div></div>
    <div class="member"><div class="img" role="img" aria-label="Agent portrait"></div><h4>Dorian Hale</h4><div class="role">Sales Agent</div><div class="socials"><span></span><span></span><span></span></div></div>
  </section>
  <section class="sec split about">
    <div><div class="photo" role="img" aria-label="Aerial photo of a leafy suburban neighbourhood"></div></div>
    <div class="red copy"><h2>About Lurro</h2><p>Lorem ipsum dolor sit amet, consectetur adipiscing elit, sed do usmod tempor incididunt ut labore et dolore magna aliqua. Quis ipsum suspendisse ultrices gravida. Risus commodo viverra cenas accumsan lacus vel facilisis. Lorem ipsum dolor sit amet, tur iscing elit. Lorem ipsum dolor sit amet, consectetur adipiscing elit, sed do usmod tempor incididunt ut labore et dolore magna aliqua. Quis ipsum suspendisse ultrices gravida.</p><span class="btn">Read more ›</span></div>
  </section>
  <section class="sec sold">
    <h2>Recently sold</h2>
    <div class="cards">
      <div class="card"><div class="img" role="img" aria-label="Aerial view of a town"><span class="tag">SOLD</span></div><div class="body"><h4>Property Name Title</h4><p>$600/mo</p><div class="meta"><span><i></i>5 Beds</span><span><i></i>2 Baths</span><span><i></i>2019</span></div></div></div>
      <div class="card"><div class="img" role="img" aria-label="Aerial view of a town"><span class="tag">SOLD</span></div><div class="body"><h4>Property Name Title</h4><p>$600/mo</p><div class="meta"><span><i></i>5 Beds</span><span><i></i>2 Baths</span><span><i></i>2019</span></div></div></div>
      <div class="card"><div class="img" role="img" aria-label="Aerial view of a town"><span class="tag">SOLD</span></div><div class="body"><h4>Property Name Title</h4><p>$600/mo</p><div class="meta"><span><i></i>5 Beds</span><span><i></i>2 Baths</span><span><i></i>2019</span></div></div></div>
    </div>
    <span class="arrow" style="left:25px;top:135px"><svg viewBox="0 0 6 6"><path d="M4 0L1 3l3 3" fill="none" stroke="currentColor"/></svg></span>
    <span class="arrow" style="right:25px;top:135px"><svg viewBox="0 0 6 6"><path d="M2 0l3 3-3 3" fill="none" stroke="currentColor"/></svg></span>
  </section>
  <section class="sec split touch">
    <div class="red copy"><h2>Get in touch</h2><div class="input">Name</div><div class="input">Email</div><div class="input">Phone</div><div class="input input--tall">Message</div><span class="btn">Submit</span></div>
    <div><div class="photo" role="img" aria-label="Photo of a happy family unpacking moving boxes"></div></div>
  </section>
  <footer class="footer">
    <div class="col1"><h5>KEEP IN TOUCH</h5><p>● Main office<br>&nbsp;&nbsp;29th floor - Lorem Ipsum<br>&nbsp;&nbsp;street - London - UK<br>✆ Call us<br>&nbsp;&nbsp;(+01) 555.019.420<br>✉ Mail to<br>&nbsp;&nbsp;hello@lurro-mail.com</p></div>
    <div class="col2"><h5>INFORMATION</h5><p>About Us<br>Contact<br>Terms &amp; Conditions<br>Recent news<br>F.A.Qs</p></div>
    <div class="col3"><h5>NEWSLETTER</h5><p>Make sure that you're always the first who receive our latest news and promotion</p><div class="sub-row"><div>Your Email Address</div><b>SEND</b></div><div class="f-icons"><span></span><span></span><span></span><span></span><span></span></div></div>
    <div class="copyright">Copyright © 2019. All Rights Reserved | Privacy Policy | Terms of Use</div>
  </footer>
</main>

</body>
</html>
```